Oil and Gas Exploration and Production company needs a business card design

We need a business card design using our logo and colors in the logo. We want a mainstream design.

```html
<!DOCTYPE html>
<html lang="en">
<head>
<meta charset="UTF-8">
<title>Norvale Energy – Business Card</title>
<link href="https://fonts.googleapis.com/css2?family=Open+Sans:wght@400;600;700;800&display=swap" rel="stylesheet">
<style>
  :root {
    --stage: #2b2b2b;
    --gold-light: #e8cf4c;
    --gold: #d4a22e;
    --gold-deep: #c8902a;
    --ink: #1f1b1a;
    --paper: #f7f7f5;
    --text: #3a3a3a;
  }
  * { box-sizing: border-box; margin: 0; padding: 0; }
  html, body {
    width: 1200px; height: 900px; overflow: hidden;
    background: var(--stage);
    font-family: "Open Sans", Arial, sans-serif;
  }
  .stage {
    width: 1200px; height: 900px;
    display: flex; flex-direction: column;
    align-items: center; justify-content: center; gap: 40px;
  }
  .card {
    width: 700px; height: 400px; position: relative; overflow: hidden;
    box-shadow: 0 10px 30px rgba(0,0,0,.45);
  }
  /* Back */
  .card-back {
    background: linear-gradient(100deg, var(--gold-light) 0%, var(--gold) 45%, var(--gold-deep) 100%);
  }
  .back-brand {
    position: absolute; left: 0; right: 0; top: 150px;
    display: flex; align-items: center; justify-content: center; gap: 14px;
  }
  .brand-dot { width: 22px; height: 22px; border-radius: 50%; background: var(--ink); }
  .back-brand .brand-name {
    font-size: 42px; font-weight: 800; color: var(--ink); letter-spacing: .5px;
  }
  .back-web {
    position: absolute; right: 50px; bottom: 40px;
    color: #fff; font-size: 15px; letter-spacing: 5px;
  }
  /* Front */
  .card-front { background: var(--paper); }
  .front-brand {
    position: absolute; left: 46px; top: 78px;
    display: flex; align-items: center; gap: 12px;
  }
  .front-brand .brand-name {
    font-size: 46px; font-weight: 800; color: var(--ink); line-height: 1;
  }
  .title-band {
    position: absolute; right: 0; top: 120px;
    width: 210px; height: 58px;
    background: var(--gold);
    padding: 8px 0 0 46px;
    border-radius: 29px 0 0 29px;
  }
  .title-dot {
    position: absolute; left: -6px; top: 3px;
    width: 52px; height: 52px; border-radius: 50%;
    background: var(--ink); border: 3px solid var(--paper);
  }
  .person-name { font-size: 17px; font-weight: 700; color: var(--ink); line-height: 1.2; }
  .person-role { font-size: 12px; font-weight: 400; color: var(--ink); letter-spacing: .5px; }
  .contact {
    position: absolute; left: 46px; top: 210px;
    list-style: none; color: var(--text); font-size: 14px; line-height: 1.35;
  }
  .contact li { display: flex; align-items: flex-start; gap: 12px; margin-bottom: 4px; }
  .contact svg { width: 14px; height: 14px; flex: none; margin-top: 2px; fill: var(--ink); }
  .contact .address { margin-bottom: 10px; }
</style>
</head>
<body>
<main class="stage">
  <section class="card card-back" aria-label="Card back">
    <div class="back-brand">
      <span class="brand-dot"></span>
      <span class="brand-name">Norvale Energy</span>
    </div>
    <p class="back-web">www.norvaleenergy.com</p>
  </section>

  <section class="card card-front" aria-label="Card front">
    <div class="front-brand">
      <span class="brand-name">Norvale Energy</span>
    </div>

    <div class="title-band">
      <span class="title-dot"></span>
      <p class="person-name">MARK ELLISON</p>
      <p class="person-role">PRESIDENT</p>
    </div>

    <ul class="contact">
      <li class="address">
        <svg viewBox="0 0 24 24"><path d="M12 2a7 7 0 0 0-7 7c0 5 7 13 7 13s7-8 7-13a7 7 0 0 0-7-7zm0 9.5A2.5 2.5 0 1 1 12 6.5a2.5 2.5 0 0 1 0 5z"/></svg>
        <span>4120 Harbor Lane<br>Millbrook, NY 12545</span>
      </li>
      <li>
        <svg viewBox="0 0 24 24"><path d="M6.6 10.8a15 15 0 0 0 6.6 6.6l2.2-2.2a1 1 0 0 1 1-.25 11.4 11.4 0 0 0 3.6.57 1 1 0 0 1 1 1V20a1 1 0 0 1-1 1A17 17 0 0 1 3 4a1 1 0 0 1 1-1h3.5a1 1 0 0 1 1 1c0 1.25.2 2.45.57 3.57a1 1 0 0 1-.25 1z"/></svg>
        <span>555 0142 2253</span>
      </li>
      <li>
        <svg viewBox="0 0 24 24"><path d="M7 1h10a2 2 0 0 1 2 2v18a2 2 0 0 1-2 2H7a2 2 0 0 1-2-2V3a2 2 0 0 1 2-2zm0 3v14h10V4zm5 15.5a1 1 0 1 0 0 2 1 1 0 0 0 0-2z"/></svg>
        <span>555 0187 5335</span>
      </li>
      <li>
        <svg viewBox="0 0 24 24"><path d="M6 2h9v5H6zM3 8h18a1 1 0 0 1 1 1v11a1 1 0 0 1-1 1H3a1 1 0 0 1-1-1V9a1 1 0 0 1 1-1zm3 4v2h6v-2zm0 4v2h6v-2zm10-4v6h3v-6z"/></svg>
        <span>555 0163 3856</span>
      </li>
      <li>
        <svg viewBox="0 0 24 24"><path d="M2 5h20v14H2zm2 2v.5l8 5 8-5V7zm0 3v7h16v-7l-8 5z"/></svg>
        <span>info@norvaleenergy.com</span>
      </li>
      <li>
        <svg viewBox="0 0 24 24"><path d="M12 2a10 10 0 1 0 0 20 10 10 0 0 0 0-20zm6.9 9h-3a15 15 0 0 0-1.3-5.6A8 8 0 0 1 18.9 11zM12 4.1c.9 1.2 1.7 3.6 1.9 6.9h-3.8c.2-3.3 1-5.7 1.9-6.9zM9.4 5.4A15 15 0 0 0 8.1 11h-3a8 8 0 0 1 4.3-5.6zM5.1 13h3a15 15 0 0 0 1.3 5.6A8 8 0 0 1 5.1 13zm6.9 6.9c-.9-1.2-1.7-3.6-1.9-6.9h3.8c-.2 3.3-1 5.7-1.9 6.9zm2.6-1.3a15 15 0 0 0 1.3-5.6h3a8 8 0 0 1-4.3 5.6z"/></svg>
        <span>www.norvaleenergy.com</span>
      </li>
    </ul>
  </section>
</main>
</body>
</html>
```